Construction Company

Design a clutter free business card, it can be double-sided utilizing the logo for VKM Ltd simple with all relevant contact information.

Please also a letterhead design to function for the purposes of invoicing, all mail requirements, with header to be distinctive while the footer ties page together and incorporates all necessary information.

For now, please use generic / dummy text and when a winner is selected, I will disclose the contact information.

Hi Designers! Please read the updated brief which includes the design of a business card and letterhead. Thank you!

```html
<!DOCTYPE html>
<html lang="en">
<head>
<meta charset="utf-8">
<title>VKM Ltd — Business Card</title>
<link rel="stylesheet" href="https://fonts.googleapis.com/css2?family=Poppins:wght@400;500&display=swap">
<style>
  :root {
    --page-bg: #e9e9ea;
    --card-white: #ffffff;
    --brand-blue: #0a2f9a;
    --brand-gold: #b8961a;
    --text-grey: #454545;
    --rule-grey: #5a5a5a;
    --back-light: #0c3fc4;
    --back-dark: #03217f;
  }
  * { box-sizing: border-box; margin: 0; padding: 0; }
  html, body { width: 1200px; height: 1200px; overflow: hidden; }
  body {
    background: var(--page-bg);
    font-family: "Poppins", sans-serif;
    position: relative;
  }
  .card {
    position: absolute;
    left: 262px;
    width: 686px;
    height: 392px;
    border-radius: 19px;
    overflow: hidden;
  }
  .card--front { top: 165px; background: var(--card-white); }
  .card--back {
    top: 653px;
    background: linear-gradient(90deg, var(--back-light) 0%, #0633a8 50%, var(--back-dark) 100%);
  }
  .brand {
    position: absolute;
    right: 46px;
    top: 58px;
    display: flex;
    align-items: center;
    gap: 12px;
    color: var(--brand-blue);
    font-weight: 500;
    font-size: 58px;
    line-height: 1;
    letter-spacing: -1px;
  }
  .brand__dot {
    width: 16px; height: 16px;
    border-radius: 50%;
    background: var(--brand-gold);
  }
  .holder { position: absolute; left: 38px; top: 240px; }
  .holder__name {
    color: var(--brand-blue);
    font-weight: 500;
    font-size: 22px;
    line-height: 1.15;
    letter-spacing: 0.2px;
  }
  .holder__title {
    color: var(--brand-gold);
    font-size: 16px;
    line-height: 1.2;
  }
  .rule {
    position: absolute;
    left: 38px; top: 293px;
    width: 600px; height: 1px;
    background: var(--rule-grey);
  }
  .contact {
    position: absolute;
    top: 311px;
    color: var(--text-grey);
    font-size: 15.5px;
    line-height: 20px;
  }
  .contact--address { left: 38px; }
  .contact--phone { left: 284px; }
  .contact--web { left: 477px; }
  .contact__row { display: flex; align-items: center; gap: 9px; }
  .contact__icon { width: 13px; height: 13px; flex: none; fill: var(--brand-blue); }
  .pattern {
    position: absolute; inset: 0;
  }
</style>
</head>
<body>
  <section class="card card--front">
    <div class="brand"><span>VKM Ltd</span><span class="brand__dot"></span></div>

    <div class="holder">
      <p class="holder__name">DANIEL HARPER</p>
      <p class="holder__title">President</p>
    </div>

    <div class="rule"></div>

    <div class="contact contact--address">
      <p>4120 Cedar Ridge Road</p>
      <p>Fairview, Oregon 97024</p>
    </div>

    <div class="contact contact--phone">
      <p class="contact__row">
        <svg class="contact__icon" viewBox="0 0 24 24"><path d="M6.6 10.8a15.1 15.1 0 0 0 6.6 6.6l2.2-2.2a1 1 0 0 1 1-.25 11.4 11.4 0 0 0 3.6.57 1 1 0 0 1 1 1V20a1 1 0 0 1-1 1A17 17 0 0 1 3 4a1 1 0 0 1 1-1h3.5a1 1 0 0 1 1 1c0 1.25.2 2.45.57 3.6a1 1 0 0 1-.25 1z"/></svg>
        555-208-4417
      </p>
      <p class="contact__row">
        <svg class="contact__icon" viewBox="0 0 24 24"><path d="M7 1h10a2 2 0 0 1 2 2v18a2 2 0 0 1-2 2H7a2 2 0 0 1-2-2V3a2 2 0 0 1 2-2zm0 3v15h10V4z"/></svg>
        555-731-0962
      </p>
    </div>

    <div class="contact contact--web">
      <p class="contact__row">
        <svg class="contact__icon" viewBox="0 0 24 24"><path d="M2 5h20v14H2zm2 2v.5l8 5 8-5V7zm0 2.8V17h16V9.8l-8 5z"/></svg>
        info@vkmltd.com
      </p>
      <p class="contact__row">
        <svg class="contact__icon" viewBox="0 0 24 24"><path d="M12 2a10 10 0 1 0 0 20 10 10 0 0 0 0-20zm-1 17.9A8 8 0 0 1 4.1 11L9 16v1a2 2 0 0 0 2 2zm6.9-2.5A2 2 0 0 0 16 16h-1v-3a1 1 0 0 0-1-1H8v-2h2a1 1 0 0 0 1-1V7h2a2 2 0 0 0 2-2v-.4a8 8 0 0 1 2.9 12.8z"/></svg>
        www.vkmltd.com
      </p>
    </div>
  </section>

  <section class="card card--back">
    <div class="pattern" role="img" aria-label="Repeating floral line pattern in blue tones, fading from light blue on the left to dark navy on the right"></div>
  </section>
</body>
</html>
```